Call Center In Need of Website Design

We are a call center that provides inbound and outbound calling & marketing services for eCommerce store. We would like to see a fun, creative, playful design that is simple.

Here are some sample design sites we like;
- https://www.velmoreline.com/
- https://pindrask.io/
- https://www.glimbertic.com/live-chat-software/
- https://www.zavrolin.com/

Here are some competitor sites;
- https://www.ostrevaglinks.com/
- https://www.helpkestrel.com/

I have attached website content for your use.

Target Market(s)

eCommerce

Coding

Coded - Design and coding required

Number of Pages Required

5+ page

Font styles to use
Sans Serif

Colors

Designer to choose colors to be used in the design.

Requirements
Must have
• Must have designs for the following 5 separate pages;
• 1. Home (landing)
• - This will be were the design style really needs to show.
• - Just needs to touch on key services
• - CTA
• 2. About Us
• - Basic page for about me paragraph
• 3. Services
• - List of services with icons
• - Click on service type to expand details or hover over service icon to view popup bubble with details about that service
• 4. Pricing
• - Option to bundle 1(one) digital service plan and 1(one) call center service plan
• - Bundling adds 10% monthly discount to over all price
• - Customer does NOT have to bundle
• - FAQ
• 5. Contact Us
• - Include a capture form (name, company name, email, phone, message)
• - Contact info
• - Business hours
• When customer purchases their desired plan, then they are taken to a page where they must schedule a call with an account rep.
Nice to have
• home page animations
Should not have
• All information on Home/Landing page.

```html
<!DOCTYPE html>
<html lang="en">
<head>
<meta charset="utf-8">
<title>Lunavox — Digital &amp; Call Center Services</title>
<link href="https://fonts.googleapis.com/css2?family=Montserrat:wght@400;500&family=Muli:wght@400&family=Open+Sans:wght@400&display=swap" rel="stylesheet">
<style>
  :root {
    --teal: #4cc0a2;
    --teal-card: #78c9b1;
    --teal-btn: #5a9e8a;
    --mint: #e3f6f1;
    --mint-deep: #d6f1ea;
    --slate: #434c4a;
    --slate-btn: #2f3634;
    --ink: #1d2321;
    --text: #444;
    --white: #fff;
  }
  * { box-sizing: border-box; margin: 0; padding: 0; }
  html, body { width: 965px; height: 1200px; overflow: hidden; background: var(--white); }
  body { position: relative; font-family: "Montserrat", sans-serif; color: var(--text); }

  .hero-bg {
    position: absolute; left: 0; top: 0; width: 965px; height: 520px;
    background: linear-gradient(180deg, #fff 0%, #fff 45%, var(--mint-deep) 100%);
    clip-path: ellipse(720px 510px at 50% 0%);
  }
  .hero-edge { position: absolute; left: 0; top: 430px; width: 965px; height: 90px; }

  .lower-bg { position: absolute; left: 0; top: 800px; width: 965px; height: 306px; }

  .header { position: absolute; left: 0; top: 0; width: 965px; height: 80px; }
  .brand { position: absolute; left: 146px; top: 20px; display: flex; align-items: center; gap: 12px; }
  .brand-mark { width: 34px; height: 34px; border: 2px solid var(--teal); border-radius: 50%; }
  .brand-name { font-size: 21px; font-weight: 400; letter-spacing: 3px; color: #555d5b; }
  .nav { position: absolute; top: 32px; left: 407px; display: flex; gap: 0; }
  .nav a { font-size: 11.5px; color: var(--ink); text-decoration: none; margin-right: 32px; }
  .nav a.active { color: var(--teal); }

  .hero-copy { position: absolute; left: 150px; top: 180px; width: 300px; }
  .hero-title { font-size: 25px; font-weight: 400; line-height: 33px; color: var(--ink); }
  .hero-title span { color: var(--teal); display: block; }
  .hero-lead { font-family: "Open Sans", sans-serif; font-size: 13px; line-height: 20px; color: #555; margin-top: 16px; }
  .btn {
    display: inline-flex; align-items: center; justify-content: center;
    width: 107px; height: 32px; border-radius: 16px;
    font-size: 11.5px; color: var(--white); text-decoration: none;
  }
  .hero-copy .btn { background: var(--teal); margin-top: 19px; margin-left: -3px; }

  .hero-art {
    position: absolute; left: 467px; top: 115px; width: 358px; height: 272px;
    background: radial-gradient(ellipse at 55% 60%, #bfe9dd 0%, #e6f6f1 55%, rgba(255,255,255,0) 80%);
    border-radius: 12px;
  }

  .welcome { position: absolute; left: 0; top: 548px; width: 965px; text-align: center; }
  .welcome-mark { width: 28px; height: 28px; margin: 0 auto; border: 2px solid var(--teal); border-radius: 50%; }
  .welcome h2 { font-size: 22px; font-weight: 400; color: var(--ink); margin-top: 15px; letter-spacing: .3px; }
  .welcome p { font-family: "Open Sans", sans-serif; font-size: 13px; line-height: 20px; width: 590px; margin: 10px auto 0; color: #555; }

  .card {
    position: absolute; top: 753px; width: 292px; height: 282px; border-radius: 3px;
    text-align: center; color: var(--white);
    box-shadow: 0 2px 4px rgba(0,0,0,.12);
  }
  .card.digital { left: 183px; background: var(--teal-card); }
  .card.calls { left: 498px; background: var(--slate); }
  .card-icon {
    position: absolute; left: 103px; top: -33px; width: 86px; height: 86px; border-radius: 50%;
    background: var(--teal); border: 4px solid var(--white);
    box-shadow: 0 3px 5px rgba(0,0,0,.18);
    display: flex; align-items: center; justify-content: center;
  }
  .card.calls .card-icon { top: -28px; }
  .card h3 { font-size: 17px; font-weight: 400; margin-top: 64px; }
  .card ul { list-style: none; margin-top: 11px; }
  .card li { font-family: "Muli", sans-serif; font-size: 10px; line-height: 20.5px; }
  .card li::before { content: "›"; font-weight: 700; font-size: 13px; margin-right: 4px; }
  .card .btn { position: absolute; left: 92px; top: 231px; }
  .card.digital .btn { background: var(--teal-btn); }
  .card.calls .btn { background: var(--slate-btn); }

  .footer { position: absolute; left: 0; top: 1106px; width: 965px; height: 94px; background: var(--white); }
  .footer-nav { position: absolute; left: 153px; top: 28px; display: flex; }
  .footer-nav a { font-size: 10.5px; color: var(--ink); text-decoration: none; margin-right: 28px; }
  .copyright { position: absolute; left: 153px; top: 52px; font-size: 8px; color: #444; }
  .social { position: absolute; left: 707px; top: 25px; display: flex; gap: 4px; }
  .social span { width: 24px; height: 24px; border: 1.5px solid var(--teal); border-radius: 50%; }
</style>
</head>
<body>
  <div class="hero-bg"></div>
  <svg class="hero-edge" viewBox="0 0 965 90" aria-hidden="true">
    <path d="M0 10 Q482 150 965 10" fill="none" stroke="#cfd8d5" stroke-width="1.2"/>
  </svg>

  <svg class="lower-bg" viewBox="0 0 965 306" preserveAspectRatio="none" aria-hidden="true">
    <path d="M0 90 Q482 -60 965 90 L965 306 L0 306 Z" fill="#e3f6f1"/>
  </svg>

  <header class="header">
    <div class="brand"><span class="brand-mark"></span><span class="brand-name">LUNAVOX</span></div>
    <nav class="nav">
      <a class="active" href="#">HOME</a>
      <a href="#">ABOUT US</a>
      <a href="#">SERVICES</a>
      <a href="#">PRICING</a>
      <a href="#">CONTACT US</a>
    </nav>
  </header>

  <section class="hero-copy">
    <h1 class="hero-title">DIGITAL &amp; CALL CENTER<span>SERVICES EXPERT</span></h1>
    <p class="hero-lead">Curabitur iaculis tempus eros Curabitur vel mi sit amet magna malesuada ultrices</p>
    <a class="btn" href="#">Learn More</a>
  </section>

  <div class="hero-art" role="img" aria-label="Illustration of call center agents with headsets, a monitor, emails, chat bubbles and checklists"></div>

  <section class="welcome">
    <div class="welcome-mark"></div>
    <h2>WELCOME TO LUNAVOX</h2>
    <p>Lunavox is an omnichannel provider for customer care and back-end office support. We primarily work with eCommerce companies around the world. Our service is vital to the core operations and functionality of consumer-focused online eCommerce companies.</p>
  </section>

  <article class="card digital">
    <div class="card-icon">
      <svg width="40" height="34" viewBox="0 0 40 34" fill="none" stroke="#fff" stroke-width="1.6" aria-hidden="true">
        <rect x="6" y="4" width="28" height="20" rx="1"/>
        <path d="M2 27 H38 L36 30 H4 Z"/>
        <path d="M11 17 H29 M11 20 H25"/>
        <path d="M14 8 L24 5 V14 L14 11 Z"/>
      </svg>
    </div>
    <h3>Digital Services</h3>
    <ul>
      <li>Email Support</li>
      <li>Live Chat Support</li>
      <li>Product Research</li>
      <li>Product Listing</li>
      <li>Price Monitoring</li>
      <li>Product Photo &amp; Video Editing</li>
    </ul>
    <a class="btn" href="#">Learn More</a>
  </article>

  <article class="card calls">
    <div class="card-icon">
      <svg width="36" height="40" viewBox="0 0 36 40" fill="none" stroke="#fff" stroke-width="1.8" aria-hidden="true">
        <path d="M6 22 V16 A12 12 0 0 1 30 16 V22"/>
        <rect x="3" y="19" width="6" height="11" rx="2"/>
        <rect x="27" y="19" width="6" height="11" rx="2"/>
        <path d="M30 30 Q30 36 22 36"/>
        <circle cx="20" cy="36" r="2"/>
      </svg>
    </div>
    <h3>Call Center Services</h3>
    <ul>
      <li>Answering service</li>
      <li>Welcome Calls</li>
      <li>Follow-Up Service</li>
      <li>Customer Upselling</li>
      <li>Over-The-Phone Order Taking</li>
      <li>Order Return Processing</li>
    </ul>
    <a class="btn" href="#">Learn More</a>
  </article>

  <footer class="footer">
    <nav class="footer-nav">
      <a href="#">HOME</a>
      <a href="#">ABOUT US</a>
      <a href="#">SERVICES</a>
      <a href="#">PRICING</a>
      <a href="#">CONTACT US</a>
    </nav>
    <p class="copyright">© 2018 Company Name&nbsp; All right reserved</p>
    <div class="social" aria-label="Social links"><span></span><span></span><span></span><span></span></div>
  </footer>
</body>
</html>
```